Moravel Aesthetic Doctor

I require an elegant, luxurious looking business card for my aesthetic business. I am a doctor and that will set me aside from competitors. I am planning to provide home and spa based treatments to clients with high expectations. I have attached my logo.

```html
<!DOCTYPE html>
<html lang="en">
<head>
<meta charset="utf-8">
<title>Moravel Aesthetic Doctor – Business Card</title>
<link href="https://fonts.googleapis.com/css2?family=Roboto:wght@300;400;500;700&display=swap" rel="stylesheet">
<style>
  :root {
    --backdrop: #8a8a8a;
    --card: #ffffff;
    --ink-grey: #9a9b9f;
    --ink-dark: #7b7c80;
    --accent: #5bbbe6;
    --accent-soft: #7ccaec;
    --rule: #8d8e92;
  }
  * { margin: 0; padding: 0; box-sizing: border-box; }
  html, body { width: 1200px; height: 1200px; overflow: hidden; }
  body {
    background: var(--backdrop);
    font-family: "Roboto", Arial, sans-serif;
    position: relative;
  }
  .card {
    position: absolute;
    top: 303px;
    width: 368px;
    height: 594px;
    background: var(--card);
    box-shadow: 2px 3px 6px rgba(0,0,0,0.35);
    overflow: hidden;
  }
  .card--front { left: 216px; display: flex; flex-direction: column; gap: 3px; }
  .card--back { left: 616px; text-align: center; }

  .photo-band { width: 100%; }
  .photo-band--diffusers { height: 139px; background: linear-gradient(180deg, #d9d6d3 0%, #efeceb 55%, #cfc9c5 100%); }
  .photo-band--towel { height: 148px; background: linear-gradient(180deg, #dcdde0 0%, #e9e9ea 60%, #8a5e3f 86%, #6d4a33 100%); }
  .photo-band--treatment { height: 149px; background: linear-gradient(90deg, #6b5a55 0%, #e8bfb8 35%, #d8a8a2 60%, #2c3550 100%); }
  .photo-band--products { height: 149px; background: linear-gradient(135deg, #ecebea 0%, #e2dfdc 50%, #3c3b3a 85%, #2a2a2a 100%); }

  .brand {
    position: absolute;
    top: 118px;
    left: 0; right: 0;
    display: flex;
    align-items: center;
    justify-content: center;
    gap: 12px;
  }
  .brand-dot { width: 56px; height: 56px; border-radius: 50%; background: var(--accent); flex: none; }
  .brand-name {
    font-weight: 400;
    color: var(--accent);
    font-size: 19px;
    line-height: 1.2;
    letter-spacing: 1.5px;
    text-transform: uppercase;
    text-align: left;
  }

  .credentials { position: absolute; top: 326px; left: 0; right: 0; }
  .doctor-name { font-weight: 700; font-size: 24px; color: var(--ink-grey); }
  .doctor-name .postnominals { font-weight: 400; font-size: 15px; color: var(--accent); }
  .qualification { font-weight: 400; font-size: 17px; color: var(--accent-soft); line-height: 21px; margin-top: 2px; }

  .divider { position: absolute; left: 0; right: 0; display: flex; align-items: center; justify-content: center; gap: 4px; }
  .divider::before, .divider::after { content: ""; width: 52px; height: 1px; background: var(--rule); margin: 0 2px; }
  .divider--contact { top: 411px; }
  .divider--social { top: 532px; }

  .contact-icon { width: 25px; height: 25px; background: var(--accent-soft); border-radius: 3px; display: flex; align-items: center; justify-content: center; }

  .contact-list { position: absolute; top: 449px; left: 0; right: 0; list-style: none; }
  .contact-list li { font-weight: 300; font-size: 16px; color: var(--ink-dark); line-height: 21.5px; }

  .social-handle { font-weight: 400; font-size: 13px; color: var(--ink-dark); padding: 0 4px; }
</style>
</head>
<body>
  <section class="card card--front" aria-label="Card front">
    <div class="photo-band photo-band--diffusers" role="img" aria-label="Photo of reed diffusers, amber bottles and white flowers"></div>
    <div class="photo-band photo-band--towel" role="img" aria-label="Photo of rolled spa towel, candle and bowl of bath salts on wood"></div>
    <div class="photo-band photo-band--treatment" role="img" aria-label="Photo of a facial treatment with gloved hands"></div>
    <div class="photo-band photo-band--products" role="img" aria-label="Photo of serum bottle, clay powder and brush on marble"></div>
  </section>

  <section class="card card--back" aria-label="Card back">
    <div class="brand">
      <span class="brand-dot" aria-hidden="true"></span>
      <span class="brand-name">Moravel<br>Aesthetic Doctor</span>
    </div>

    <div class="credentials">
      <p class="doctor-name">Dr Elise Varant <span class="postnominals">MRCPCH MD</span></p>
      <p class="qualification">Australasian Diploma of<br>Aesthetic Medicine</p>
    </div>

    <div class="divider divider--contact">
      <span class="contact-icon" aria-label="Phone">
        <svg width="15" height="15" viewBox="0 0 24 24"><path fill="#fff" d="M6.6 10.8a15 15 0 0 0 6.6 6.6l2.2-2.2a1 1 0 0 1 1-.25 11.4 11.4 0 0 0 3.6.57 1 1 0 0 1 1 1V20a1 1 0 0 1-1 1A17 17 0 0 1 3 4a1 1 0 0 1 1-1h3.5a1 1 0 0 1 1 1c0 1.25.2 2.45.57 3.57a1 1 0 0 1-.25 1z"/></svg>
      </span>
      <span class="contact-icon" aria-label="Email">
        <svg width="15" height="12" viewBox="0 0 24 18"><rect x="1" y="1" width="22" height="16" fill="none" stroke="#fff" stroke-width="2"/><path d="M1 1l11 9 11-9" fill="none" stroke="#fff" stroke-width="2"/></svg>
      </span>
      <span class="contact-icon" aria-label="Website">
        <svg width="15" height="15" viewBox="0 0 24 24"><circle cx="12" cy="12" r="10" fill="none" stroke="#fff" stroke-width="2"/><path d="M2 12h20M12 2c3 3 3 17 0 20M12 2c-3 3-3 17 0 20" fill="none" stroke="#fff" stroke-width="1.6"/></svg>
      </span>
    </div>

    <ul class="contact-list">
      <li>0800 555 014</li>
      <li>elise@moravel.co.nz</li>
      <li>www.moravel.co.nz</li>
    </ul>

    <div class="divider divider--social">
      <span class="social-handle">@moravelaesthetic</span>
    </div>
  </section>
</body>
</html>
```